Business Card Design Project

I require a business card with the following information on them for various different people;
name
m:
f:
e:
I have a logo already and will attached that. We are in the construction industry. I require something clean and simple but eye catching at the same time. You can use another colour with our logo if you like and you can style the logo as well if you wish. I am open.
Also it needs to be front and back design.
Industry/Entity Type
Construction
Requirements
Must have
- Logo, name, mobile, fax and email address.
Front and back design

```html
<!DOCTYPE html>
<html lang="en">
<head>
<meta charset="utf-8">
<title>Northvale Developments – Business Card</title>
<link rel="stylesheet" href="https://fonts.googleapis.com/css2?family=Questrial&family=Arimo&family=Roboto+Condensed&display=swap">
<style>
  :root {
    --paper: #ffffff;
    --crop: #1a1a1a;
    --card-edge: #566059;
    --card-core: #242825;
    --brand-green: #7de02a;
    --accent-lime: #a6e83a;
    --band-black: #0b0d0c;
    --band-silver: #c6ccc6;
    --text-light: #ffffff;
  }
  html, body {
    margin: 0;
    padding: 0;
    width: 1200px;
    height: 887px;
    overflow: hidden;
    background: var(--paper);
  }
  .sheet { display: block; width: 1200px; height: 887px; }
  .crop-mark { stroke: var(--crop); stroke-width: 1.2; }
  .brand-name {
    font-family: "Questrial", sans-serif;
    fill: var(--brand-green);
    font-weight: 400;
  }
  .person-name {
    font-family: "Arimo", sans-serif;
    font-size: 37px;
    fill: var(--brand-green);
  }
  .contact-line {
    font-family: "Roboto Condensed", sans-serif;
    font-size: 24px;
    fill: var(--text-light);
  }
  .contact-icon { fill: none; stroke: var(--brand-green); stroke-width: 2; }
  .contact-icon-solid { fill: var(--brand-green); }
</style>
</head>
<body>
<svg class="sheet" viewBox="0 0 1200 887" xmlns="http://www.w3.org/2000/svg">
  <defs>
    <linearGradient id="card-shade" x1="0" y1="0" x2="1" y2="0">
      <stop offset="0" stop-color="var(--card-edge)"/>
      <stop offset="0.25" stop-color="var(--card-core)"/>
      <stop offset="0.6" stop-color="var(--card-core)"/>
      <stop offset="1" stop-color="var(--card-edge)"/>
    </linearGradient>
    <linearGradient id="name-rule" x1="0" y1="0" x2="1" y2="0">
      <stop offset="0" stop-color="#111"/>
      <stop offset="0.5" stop-color="#8a8f8b"/>
      <stop offset="1" stop-color="#111"/>
    </linearGradient>
    <clipPath id="card-shape">
      <rect x="181" y="181" width="838" height="524" rx="40"/>
    </clipPath>
  </defs>

  <g class="crop-marks">
    <line class="crop-mark" x1="181" y1="0" x2="181" y2="121"/>
    <line class="crop-mark" x1="1019" y1="0" x2="1019" y2="121"/>
    <line class="crop-mark" x1="181" y1="766" x2="181" y2="887"/>
    <line class="crop-mark" x1="1019" y1="766" x2="1019" y2="887"/>
    <line class="crop-mark" x1="0" y1="181" x2="121" y2="181"/>
    <line class="crop-mark" x1="1079" y1="181" x2="1200" y2="181"/>
    <line class="crop-mark" x1="0" y1="705" x2="121" y2="705"/>
    <line class="crop-mark" x1="1079" y1="705" x2="1200" y2="705"/>
  </g>

  <g class="card" clip-path="url(#card-shape)">
    <rect class="card-background" x="181" y="181" width="838" height="524" fill="url(#card-shade)"/>

    <g class="brand-lockup">
      <rect x="468" y="272" width="22" height="22" fill="var(--brand-green)"/>
      <text class="brand-name" x="502" y="300" font-size="50">Northvale</text>
      <text class="brand-name" x="610" y="400" font-size="32" text-anchor="middle" letter-spacing="1">DEVELOPMENTS</text>
    </g>

    <text class="person-name" x="232" y="463">Martin Hale</text>
    <rect x="181" y="468" width="367" height="2" fill="url(#name-rule)"/>

    <g class="contact-list">
      <g class="contact-icon-mobile">
        <rect class="contact-icon-solid" x="233" y="489" width="14" height="24" rx="3"/>
        <rect x="236" y="494" width="8" height="7" fill="var(--card-core)"/>
      </g>
      <text class="contact-line" x="271" y="512">0400 123 456</text>

      <g class="contact-icon-fax">
        <rect class="contact-icon" x="231" y="530" width="19" height="14" rx="2"/>
        <rect class="contact-icon" x="235" y="523" width="11" height="7"/>
        <line class="contact-icon" x1="235" y1="537" x2="246" y2="537"/>
      </g>
      <text class="contact-line" x="271" y="544">03 9000 4521</text>

      <g class="contact-icon-email">
        <rect class="contact-icon" x="232" y="563" width="21" height="13"/>
        <polyline class="contact-icon" points="232,563 242.5,571 253,563"/>
      </g>
      <text class="contact-line" x="271" y="576">martin@northvale.com.au</text>
    </g>

    <polygon class="accent-lime-band" points="601,582 1019,582 1019,595 588,595" fill="var(--accent-lime)"/>
    <rect class="band-black" x="181" y="595" width="838" height="50" fill="var(--band-black)"/>
    <polygon class="band-silver" points="270,647 1019,647 1019,663 285,663" fill="var(--band-silver)"/>
  </g>
</svg>
</body>
</html>
```